Design a Website in Wordpress for an Australian Health Training Company in Health related courses

We require a WORDPRESS based Website (due to add on's we need to use for third party software) to replace our old site.
We offer national face to face delivery in medical reception, terminology and also administration.
The website will have around 6 pages and the ability to describe our main 6 courses (perhaps on the Courses page this may be tabs opening up to details for example?)
I have attached a previous sample of a Joomla site which was being developed (please do not feel you have to copy this - but I am just giving it as a sample - copying would be boring). But it gives an idea of look/feel and colours which may be suitable. Open to other ideas though.
I will provide some of the content, but would like the ability to finish the content myself.
Images and graphics are important. While a few medical photos re great - don't be tempted to us all pictures of doctors and nurses (although a couple would be good) - these are administrative courses so general corporate, eye catching visionary pictures of people in general are great. A medical type picture is also fine.
THE BOOKING system - will be via an ADD ON which will occur at the end of the project and is supplied by a third party software company (our student management system). This project will include up to 2 hours working with the Tech guys from the third party software to enable the ADD ON. If this ADD ON requires more time, we will pay hourly (although I do not expect it will).
Target Market(s)
Mostly a female market, many mature aged women target 25-45 yrs. Mixture of medical/health and corporate. Maybe a bit of mums returning to work and corporate inspiration.
Industry/Entity Type
It Company
Coding
Coded - Design and coding required
Number of Pages Required
5+ page
Requirements
Must have
- Wordpress
- Great graphics
- Interesting
- professional and clean
- Enquiry section (info Pak)
- Should have a University feel to it - Education
- Pages
- Home Page - About Us - Recruitment -Courses - Class Schedule - Traineeships Queensland Funding - Latest News Blog - Corporate Training- Contact us

```html
<!DOCTYPE html>
<html lang="en">
<head>
<meta charset="utf-8">
<title>Harbour Institute of Training</title>
<link href="https://fonts.googleapis.com/css2?family=Raleway:wght@400;500;600;700&family=Open+Sans:wght@400;600;700&display=swap" rel="stylesheet">
<style>
:root{
  --navy:#2e4168;
  --navy-dark:#253756;
  --orange:#f7963a;
  --orange-soft:#f9a953;
  --text:#5a5a5a;
  --muted:#8a8a8a;
  --white:#ffffff;
  --line:#e4e4e4;
}
*{box-sizing:border-box;margin:0;padding:0}
html,body{width:1200px;height:3448px;overflow:hidden}
body{font-family:"Open Sans",Arial,sans-serif;color:var(--text);background:var(--white);font-size:13px;line-height:1.6}
.wrap{width:880px;margin:0 auto;position:relative}
h1,h2,h3,h4{font-family:"Raleway",Arial,sans-serif}
a{color:inherit;text-decoration:none}

/* top bar */
.topbar{height:37px;background:var(--navy);color:var(--white);font-size:11px;font-weight:600;text-transform:uppercase}
.topbar .wrap{display:flex;justify-content:space-between;align-items:center;height:37px}
.topbar .links{display:flex;gap:22px}
.topbar .right{display:flex;align-items:center;height:37px}
.topbar .phone{display:flex;align-items:center;gap:8px;margin-right:18px;font-size:13px}
.topbar .btn{background:var(--orange);height:37px;line-height:37px;padding:0 16px;margin-left:4px}

/* nav */
.nav{height:94px;background:var(--white);position:relative;z-index:3}
.nav .wrap{height:94px}
.brand{position:absolute;left:-20px;top:-12px;width:190px;height:145px;border-radius:0 0 95px 95px;background:var(--white);display:flex;align-items:center;justify-content:center;text-align:center;padding:0 24px}
.brand span{font-family:"Raleway",Arial,sans-serif;font-weight:700;color:var(--navy);font-size:16px;line-height:1.25;text-transform:uppercase}
.menu{position:absolute;right:0;top:37px;display:flex;gap:24px;font-family:"Raleway",Arial,sans-serif;font-weight:600;font-size:11px;text-transform:uppercase;color:#333}
.menu .active{color:var(--orange)}

/* hero */
.hero{height:543px;position:relative;background:linear-gradient(120deg,#8a8f96 0%,#c9cacb 35%,#e6e2dc 55%,#9aa0a8 100%);color:var(--white);text-align:center}
.hero::after{content:"";position:absolute;inset:0;background:rgba(30,40,60,.28)}
.hero .inner{position:relative;z-index:2;padding-top:162px}
.hero h1{font-size:42px;font-weight:600;line-height:1.2;text-transform:uppercase;letter-spacing:.5px}
.hero .cta{display:inline-block;margin-top:38px;background:var(--orange);border-radius:22px;padding:12px 40px;font-family:"Raleway",Arial,sans-serif;font-size:12px;font-weight:700;text-transform:uppercase}
.hero .arrow{position:absolute;top:388px;width:34px;height:34px;border:2px solid rgba(255,255,255,.8);border-radius:50%;z-index:2;display:flex;align-items:center;justify-content:center}
.hero .arrow.prev{left:28px}.hero .arrow.next{right:28px}

/* welcome */
.welcome{height:372px;padding-top:50px}
.welcome .wrap{display:flex;gap:40px}
.welcome .photo{width:391px;height:276px;background:linear-gradient(135deg,#d9dde2,#f2f2f2 50%,#b8c0c9)}
.welcome .copy{flex:1;padding-top:4px}
.welcome h2{font-size:20px;font-weight:700;color:var(--navy);line-height:1.3;text-transform:uppercase}
.welcome p{font-size:11px;line-height:1.75;margin-top:18px}
.btn-orange{display:inline-block;background:var(--orange);color:var(--white);font-family:"Raleway",Arial,sans-serif;font-weight:700;font-size:11px;text-transform:uppercase;padding:8px 18px}
.welcome .btn-orange{margin-top:16px}

/* courses */
.courses{height:410px;background:var(--navy);color:var(--white);text-align:center;padding-top:36px}
.section-title{font-size:21px;font-weight:700;text-transform:uppercase;letter-spacing:.5px}
.courses .grid{display:flex;justify-content:space-between;margin-top:32px}
.course{width:200px}
.course svg{display:block;margin:0 auto}
.course h3{font-size:15px;font-weight:500;margin-top:22px}
.course p{font-size:10px;line-height:1.6;margin-top:10px;color:#dfe4ee}
.dots{display:flex;justify-content:center;gap:6px;margin-top:26px}
.dots i{width:9px;height:9px;border-radius:50%;background:var(--white)}
.dots i.on{background:var(--orange)}

/* blog */
.blog{height:481px;text-align:center;padding-top:34px}
.blog .section-title{color:var(--navy)}
.blog .grid{display:flex;gap:20px;margin-top:34px;text-align:left}
.post{width:280px}
.post .thumb{height:166px;background:linear-gradient(135deg,#c8ced6,#eef0f2 55%,#aab3bf)}
.post .meta{display:flex;gap:18px;font-size:10px;color:var(--orange);margin-top:14px}
.post h3{font-size:14px;font-weight:500;color:#333;margin-top:6px}
.post p{font-size:10px;line-height:1.6;margin-top:8px}
.btn-navy{display:inline-block;background:var(--navy);color:var(--white);font-size:10px;font-weight:600;padding:6px 14px;margin-top:14px}

/* info pack */
.infopack{height:402px;position:relative;background:linear-gradient(110deg,#7b8593 0%,#b7bcc3 40%,#8f96a1 70%,#5f6a7a 100%);color:var(--white);text-align:center}
.infopack::after{content:"";position:absolute;inset:0;background:rgba(34,48,78,.62)}
.infopack .inner{position:relative;z-index:2;padding-top:46px}
.infopack p{width:540px;margin:12px auto 0;font-size:10px;line-height:1.6;color:#e6e9ef}
.form{width:540px;margin:22px auto 0;display:grid;grid-template-columns:1fr 1fr;gap:10px}
.field{height:38px;background:var(--white);color:#555;font-size:10px;font-style:italic;text-align:left;padding:0 12px;line-height:38px}
.submit{height:38px;background:var(--orange);line-height:38px;font-family:"Raleway",Arial,sans-serif;font-weight:700;font-size:13px;text-transform:uppercase}

/* why */
.why{height:495px;padding-top:44px;text-align:center}
.why .section-title{color:var(--navy)}
.why .grid{position:relative;height:360px;margin-top:24px;text-align:left}
.feature{position:absolute;width:240px;display:flex;gap:18px}
.feature .ic{flex:none;width:40px;height:40px;display:flex;align-items:center;justify-content:center}
.feature h4{font-size:14px;font-weight:500;color:#333}
.feature p{font-size:10px;line-height:1.6;margin-top:4px}
.why .crest{position:absolute;left:322px;top:20px;width:236px;height:300px;display:flex;flex-direction:column;align-items:center;justify-content:center;text-align:center;gap:16px}
.why .crest .mark{width:54px;height:54px;border-radius:50%;background:var(--navy)}
.why .crest span{font-family:"Raleway",Arial,sans-serif;font-weight:700;font-size:22px;color:var(--navy);line-height:1.3;text-transform:uppercase}

/* testimonials */
.testimonials{height:287px;background:linear-gradient(180deg,var(--orange-soft),var(--orange));color:var(--white);text-align:center;padding-top:40px}
.testimonials .body{display:flex;gap:28px;align-items:center;margin-top:24px;text-align:left}
.avatar{position:relative;flex:none;width:116px;height:116px;border-radius:50%;border:4px solid var(--white);background:linear-gradient(135deg,#e8c6a8,#a36a45)}
.avatar .q{position:absolute;right:-8px;bottom:-4px;width:38px;height:38px;border-radius:50%;background:var(--navy);border:3px solid var(--white)}
.testimonials blockquote{font-size:11px;font-style:italic;line-height:1.7}
.testimonials cite{display:block;font-style:normal;font-weight:700;font-size:11px;margin-top:10px;text-transform:uppercase}
.testimonials .dots{margin-top:28px}
.testimonials .dots i{background:transparent;border:1.5px solid var(--white)}
.testimonials .dots i.on{background:var(--white)}

/* footer */
.footer{height:255px;padding-top:42px}
.footer .wrap{display:flex}
.footer .f-brand{width:235px;height:130px;display:flex;align-items:center;gap:10px;padding-right:30px}
.footer .f-brand .mark{flex:none;width:22px;height:22px;background:var(--navy)}
.footer .f-brand span{font-family:"Raleway",Arial,sans-serif;font-weight:700;color:var(--navy);font-size:15px;line-height:1.3;text-transform:uppercase}
.footer h4{font-size:13px;font-weight:700;color:#333;text-transform:uppercase}
.footer ul{list-style:none;font-size:11px;margin-top:14px;line-height:1.75}
.footer .col-links{width:152px}
.footer .col-contact{width:223px}
.footer .col-contact p{font-size:11px;line-height:1.6;margin-top:14px}
.footer .col-news{flex:1}
.footer .col-news p{font-size:11px;line-height:1.6;margin-top:14px}
.footer .email{height:32px;background:#efefef;font-size:10px;line-height:32px;padding:0 12px;margin-top:14px;width:268px}
.footer .btn-orange{margin-top:10px;font-size:10px;padding:7px 14px}

/* bottom */
.bottom{height:72px;background:var(--navy);color:var(--white);font-size:10px}
.bottom .wrap{display:flex;justify-content:space-between;align-items:center;height:72px}
.social{display:flex;gap:8px}
.social i{width:24px;height:24px;border:1.5px solid rgba(255,255,255,.75);border-radius:50%}
</style>
</head>
<body>

<header>
  <div class="topbar">
    <div class="wrap">
      <nav class="links"><a href="#">Latest News Blog</a><a href="#">Corporate Training</a><a href="#">Contact Us</a></nav>
      <div class="right">
        <span class="phone">
          <svg width="13" height="13" viewBox="0 0 24 24"><path fill="#fff" d="M6.6 10.8a15.1 15.1 0 0 0 6.6 6.6l2.2-2.2a1 1 0 0 1 1-.25 11.4 11.4 0 0 0 3.6.57 1 1 0 0 1 1 1V20a1 1 0 0 1-1 1A17 17 0 0 1 3 4a1 1 0 0 1 1-1h3.5a1 1 0 0 1 1 1c0 1.25.2 2.45.57 3.57a1 1 0 0 1-.25 1z"/></svg>
          040-555-0182
        </span>
        <a class="btn" href="#">Enrol Now</a>
        <a class="btn" href="#">Info Pack</a>
      </div>
    </div>
  </div>
  <div class="nav">
    <div class="wrap">
      <a class="brand" href="#"><span>Harbour Institute of Training</span></a>
      <nav class="menu">
        <a class="active" href="#">Home</a><a href="#">About Us</a><a href="#">Recruitment</a><a href="#">Courses</a><a href="#">Class Schedule</a><a href="#">Traineeships Queensland Funding</a>
      </nav>
    </div>
  </div>
</header>

<section class="hero" role="img" aria-label="Photo of a trainer presenting at a whiteboard to a group of students">
  <div class="inner">
    <h1>We are a health training<br>company in Australia.</h1>
    <a class="cta" href="#">Get Started Here</a>
  </div>
  <span class="arrow prev"><svg width="10" height="12" viewBox="0 0 10 12"><path d="M7 1 2 6l5 5" fill="none" stroke="#fff" stroke-width="2"/></svg></span>
  <span class="arrow next"><svg width="10" height="12" viewBox="0 0 10 12"><path d="M3 1l5 5-5 5" fill="none" stroke="#fff" stroke-width="2"/></svg></span>
</section>

<section class="welcome">
  <div class="wrap">
    <div class="photo" role="img" aria-label="Photo of two smiling colleagues working at a computer"></div>
    <div class="copy">
      <h2>Welcome to<br>Harbour Institute of Training</h2>
      <p>Harbour is Australia's leading provider of educational, training and support services for the medical and dental industry – enabling students to be immediately skilled and 'job ready' for a career in health. Harbour is a Registered Training Organisation offering specialised medical administration training in over 15 locations Australia wide. Harbour have trained thousands of students the required knowledge and skills to become successful health care administrators. Our unique Short Medical Reception and Terminology Course and our full qualification is nationally accredited and the go-to recognised qualification in industry.</p>
      <a class="btn-orange" href="#">Read More</a>
    </div>
  </div>
</section>

<section class="courses">
  <div class="wrap">
    <h2 class="section-title">Our Courses</h2>
    <div class="grid">
      <article class="course">
        <svg width="124" height="134" viewBox="0 0 124 134"><path d="M62 4 116 18v44c0 34-24 56-54 68C32 118 8 96 8 62V18z" fill="#fff"/><path d="M62 12 108 24v38c0 29-20 48-46 59C36 110 16 91 16 62V24z" fill="none" stroke="#2e4168" stroke-width="3"/><path d="M54 40h16v18h18v16H70v18H54V74H36V58h18z" fill="#2e4168"/></svg>
        <h3>Medical Terminology</h3>
        <p>Learn core medical words, cocte tur adipiscing elit, sed do eiusmod tem por incididunt ut labore et dolor.</p>
      </article>
      <article class="course">
        <svg width="124" height="134" viewBox="0 0 124 134"><path d="M62 4 116 18v44c0 34-24 56-54 68C32 118 8 96 8 62V18z" fill="#fff"/><path d="M62 12 108 24v38c0 29-20 48-46 59C36 110 16 91 16 62V24z" fill="none" stroke="#2e4168" stroke-width="3"/><rect x="32" y="50" width="60" height="30" rx="3" fill="none" stroke="#2e4168" stroke-width="3"/><g fill="#2e4168"><rect x="38" y="56" width="6" height="5"/><rect x="48" y="56" width="6" height="5"/><rect x="58" y="56" width="6" height="5"/><rect x="68" y="56" width="6" height="5"/><rect x="78" y="56" width="6" height="5"/><rect x="38" y="64" width="6" height="5"/><rect x="48" y="64" width="6" height="5"/><rect x="58" y="64" width="6" height="5"/><rect x="68" y="64" width="6" height="5"/><rect x="78" y="64" width="6" height="5"/><rect x="46" y="72" width="32" height="4"/></g></svg>
        <h3>Keyboard and Typing</h3>
        <p>Build fast typing skills, cocte tur adipiscing elit, sed do eiusmod tem por incididunt ut labore et dolor.</p>
      </article>
      <article class="course">
        <svg width="124" height="134" viewBox="0 0 124 134"><path d="M62 4 116 18v44c0 34-24 56-54 68C32 118 8 96 8 62V18z" fill="#fff"/><path d="M62 12 108 24v38c0 29-20 48-46 59C36 110 16 91 16 62V24z" fill="none" stroke="#2e4168" stroke-width="3"/><rect x="38" y="40" width="48" height="32" rx="2" fill="none" stroke="#2e4168" stroke-width="3"/><rect x="56" y="72" width="12" height="8" fill="#2e4168"/><rect x="46" y="80" width="32" height="4" fill="#2e4168"/><rect x="34" y="88" width="56" height="4" fill="#2e4168"/></svg>
        <h3>Harbour Online</h3>
        <p>Study from home online, cocte tur adipiscing elit, sed do eiusmod tem por incididunt ut labore et dolor.</p>
      </article>
      <article class="course">
        <svg width="124" height="134" viewBox="0 0 124 134"><path d="M62 4 116 18v44c0 34-24 56-54 68C32 118 8 96 8 62V18z" fill="#fff"/><path d="M62 12 108 24v38c0 29-20 48-46 59C36 110 16 91 16 62V24z" fill="none" stroke="#2e4168" stroke-width="3"/><path d="M34 44h20l6 6h30v38H34z" fill="#2e4168"/><rect x="64" y="66" width="20" height="16" rx="2" fill="#fff"/><path d="M68 66v-5a6 6 0 0 1 12 0v5" fill="none" stroke="#fff" stroke-width="3"/></svg>
        <h3>Confidentiality</h3>
        <p>Handle patient records safely, tur adipiscing elit, sed do eiusmod tem por incididunt ut labore et dolor.</p>
      </article>
    </div>
    <div class="dots"><i></i><i class="on"></i></div>
  </div>
</section>

<section class="blog">
  <div class="wrap">
    <h2 class="section-title">Latest Blog News</h2>
    <div class="grid">
      <article class="post">
        <div class="thumb" role="img" aria-label="Photo of a presenter speaking to a seated business audience"></div>
        <div class="meta"><span>June 21, 2016</span><span>Comments</span></div>
        <h3>Bonorum Maloru perspiciatis und</h3>
        <p>Sed ut perspiciatis unde omnis iste natus error sit volu ptatem accusantium doloremque laudantium, totaem aperiam, eaque ipsa quae ab illo inventore.</p>
        <a class="btn-navy" href="#">Read More</a>
      </article>
      <article class="post">
        <div class="thumb" role="img" aria-label="Photo of colleagues reviewing charts in a meeting room"></div>
        <div class="meta"><span>June 21, 2016</span><span>Comments</span></div>
        <h3>Bonorum Maloru perspiciatis und</h3>
        <p>Sed ut perspiciatis unde omnis iste natus error sit volu ptatem accusantium doloremque laudantium, totaem aperiam, eaque ipsa quae ab illo inventore.</p>
        <a class="btn-navy" href="#">Read More</a>
      </article>
      <article class="post">
        <div class="thumb" role="img" aria-label="Photo of a woman leading a boardroom discussion"></div>
        <div class="meta"><span>June 21, 2016</span><span>Comments</span></div>
        <h3>Bonorum Maloru perspiciatis und</h3>
        <p>Sed ut perspiciatis unde omnis iste natus error sit volu ptatem accusantium doloremque laudantium, totaem aperiam, eaque ipsa quae ab illo inventore.</p>
        <a class="btn-navy" href="#">Read More</a>
      </article>
    </div>
  </div>
</section>

<section class="infopack" role="img" aria-label="Photo of a smiling team seated around an office table">
  <div class="inner">
    <h2 class="section-title">Email Me an Info Pack</h2>
    <p>"Sed ut perspiciatis unde omnis iste natus error sit voluptatem accusantium doloremque laudantium, totam rem aperiam, eaque ipsa quae ab illo inventore veritatis et quasi architecto beatae vitae dicta sunt explicabo. Nemo enim ipsam voluptatem quia voluptas sit aspernatur aut odi</p>
    <div class="form">
      <div class="field">Name:</div><div class="field">State:</div>
      <div class="field">Email:</div><div class="field">Mobile:</div>
      <div class="field">Course:</div><div class="submit">Submit</div>
    </div>
  </div>
</section>

<section class="why">
  <div class="wrap">
    <h2 class="section-title">Why Harbour Institute ?</h2>
    <div class="grid">
      <div class="feature" style="left:0;top:0">
        <span class="ic"><svg width="34" height="38" viewBox="0 0 34 38"><path d="M17 1 33 6v12c0 10-7 16-16 19C8 34 1 28 1 18V6z" fill="#f7963a"/><path d="M9 16h4l8-5v16l-8-5H9z" fill="#fff"/></svg></span>
        <div><h4>Quality</h4><p>Harbour delivery quality, effective training facilitated by industry leaders. Just ask our students who rate us on average</p></div>
      </div>
      <div class="feature" style="left:0;top:118px">
        <span class="ic"><svg width="34" height="38" viewBox="0 0 34 38"><path d="M17 1 33 6v12c0 10-7 16-16 19C8 34 1 28 1 18V6z" fill="#2e4168"/><g fill="#fff"><circle cx="22" cy="12" r="3"/><circle cx="11" cy="18" r="3"/><circle cx="22" cy="24" r="3"/></g><path d="M22 12 11 18l11 6" stroke="#fff" stroke-width="1.5" fill="none"/></svg></span>
        <div><h4>Experience</h4><p>Harbour is Australia's largest and leading providers of nationally recognised training in health administration – training from</p></div>
      </div>
      <div class="feature" style="left:0;top:236px">
        <span class="ic"><svg width="34" height="38" viewBox="0 0 34 38"><path d="M17 1 33 6v12c0 10-7 16-16 19C8 34 1 28 1 18V6z" fill="#2e4168"/><rect x="9" y="11" width="16" height="14" rx="1" fill="none" stroke="#fff" stroke-width="2"/><path d="M9 15h16" stroke="#fff" stroke-width="2"/></svg></span>
        <div><h4>Value</h4><p>Our innovative teaching approach allows us to deliver exceptional training at affordable prices with no hidden extras.</p></div>
      </div>
      <div class="crest"><i class="mark"></i><span>Harbour Institute<br>of Training</span></div>
      <div class="feature" style="left:616px;top:0">
        <span class="ic"><svg width="34" height="38" viewBox="0 0 34 38"><path d="M17 1 33 6v12c0 10-7 16-16 19C8 34 1 28 1 18V6z" fill="#2e4168"/><rect x="10" y="11" width="14" height="15" fill="none" stroke="#fff" stroke-width="2"/><path d="M13 16h8M13 20h8" stroke="#fff" stroke-width="1.5"/></svg></span>
        <div><h4>Industry Recognised</h4><p>Harbour work hand in hand with industry to develop our course programme and consolidate the programme annually</p></div>
      </div>
      <div class="feature" style="left:616px;top:118px">
        <span class="ic"><svg width="34" height="38" viewBox="0 0 34 38"><path d="M17 1 33 6v12c0 10-7 16-16 19C8 34 1 28 1 18V6z" fill="#2e4168"/><rect x="9" y="14" width="16" height="11" rx="1" fill="#fff"/><rect x="13" y="10" width="8" height="5" fill="none" stroke="#fff" stroke-width="2"/></svg></span>
        <div><h4>Great Job Results</h4><p>Harbour students get jobs! Our focus is to create job-ready students who are mentored to achieve their goals.</p></div>
      </div>
      <div class="feature" style="left:616px;top:236px">
        <span class="ic"><svg width="34" height="38" viewBox="0 0 34 38"><path d="M17 1 33 6v12c0 10-7 16-16 19C8 34 1 28 1 18V6z" fill="#2e4168"/><path d="M10 18h4v8h-4zM15 26h8l2-7h-6l1-5-5 4z" fill="#fff"/></svg></span>
        <div><h4>Other</h4><p>Sed ut perspiciatis unde omnis iste natus error sit voluptatem accusantium doloremque laudantium, totam rem aperiama.</p></div>
      </div>
    </div>
  </div>
</section>

<section class="testimonials">
  <div class="wrap">
    <h2 class="section-title">Client Testimonials</h2>
    <div class="body">
      <div class="avatar" role="img" aria-label="Portrait photo of a smiling graduate"><span class="q"></span></div>
      <div>
        <blockquote>“ I completed the course on Feb 13th. Loved it. The trainers, Clare and Meg were excellent in their delivery and knowledge. I want to say a huge thank you for the course and knowledge I came away with. I have secured a fantastic job after my first application! Such good value for money too! I would highly recommend it. I'm a mature age person so it's never too late to up-skill yourself to get what you deserve! ”</blockquote>
        <cite>Jane Miller, City Name</cite>
      </div>
    </div>
    <div class="dots"><i></i><i></i><i class="on"></i><i></i><i></i></div>
  </div>
</section>

<footer>
  <div class="footer">
    <div class="wrap">
      <div class="f-brand"><i class="mark"></i><span>Harbour Institute of Training</span></div>
      <div class="col-links">
        <h4>Links</h4>
        <ul><li>Home</li><li>About Us</li><li>Recruitment</li><li>Courses</li><li>Class Schedule</li><li>Latest News</li><li>Training</li></ul>
      </div>
      <div class="col-contact">
        <h4>Contact Us</h4>
        <p>New South Wales, Victoria &amp; ACT<br>1800 555 010</p>
        <p>South Australia, Queensland, NT<br>1800 555 020</p>
        <p>Western Australia<br>08 5550 3000</p>
      </div>
      <div class="col-news">
        <h4>Newsletter</h4>
        <p>Lorem ipsum dolor sit amet adipiscing ed do elusm dunt ut labore etagna aliquat enimnim ven</p>
        <div class="email">Email:</div>
        <a class="btn-orange" href="#">Submit Here</a>
      </div>
    </div>
  </div>
  <div class="bottom">
    <div class="wrap">
      <div class="social"><i></i><i></i><i></i><i></i></div>
      <span>© 2016 Harbour Institute of Training. All copyrights are reserved.</span>
    </div>
  </div>
</footer>

</body>
</html>
```